Baseball Coaching Camp for 5-14year olds needs sales campaign

Local baseball coaching camp for children is in it's 22nd year running a 4-5 week series of summer camps. Each year we use email marketing beginning around December to sell our camps to the parents to sign up their children for one or more weeks. All information about the camps can be seen on our website at https://hemmingtarn.com/. In the past we have had success by changing the look of the emails each month and offering a decreasing discount as the camps get closer.

Our target market is the parents of children ages 5-14years old who like and play baseball and are interested in improving their skills in a fun environment during the Summer months.

We would like to improve the sales by developing new creative and imaginative emails for this season. We need 6 to 8 quality ads that can somehow relate to each other , these ads will be sent via our mailing list as well as used on social media. One of the owners thought it would be nice to use the "river of lanterns" theme though we are open to all ideas.
We have given you access to a dropbox link with examples of past campaigns along with artwork and images here
https://www.filequay.net/sh/q7ptr2mzk4wnhd/BBReo-kmTulf5pLXU318jw6Hb?dl=0

```html
<!DOCTYPE html>
<html lang="en">
<head>
<meta charset="utf-8">
<title>Hemmingtarn Baseball Camp</title>
<link href="https://fonts.googleapis.com/css2?family=Bebas+Neue&family=Oswald:wght@400;500&family=Barlow:wght@400;500;600&family=Roboto:wght@400&display=swap" rel="stylesheet">
<style>
  :root {
    --navy: #2e3a8c;
    --yellow: #f0ec2e;
    --gold: #f4e61f;
    --ink: #3d3d3d;
    --muted: #555555;
    --footer: #2b2b2b;
    --white: #ffffff;
  }
  * { margin: 0; padding: 0; box-sizing: border-box; }
  html, body { width: 1200px; height: 3704px; overflow: hidden; background: var(--white); }
  body { position: relative; font-family: "Barlow", sans-serif; color: var(--ink); }

  .site-header { position: absolute; top: 0; left: 0; width: 1200px; height: 204px; display: flex; align-items: center; justify-content: center; gap: 18px; }
  .brand-dot { width: 34px; height: 34px; border-radius: 50%; background: var(--navy); }
  .brand-name { font-family: "Bebas Neue", sans-serif; font-size: 92px; color: var(--navy); letter-spacing: 2px; line-height: 1; }

  .hero { position: absolute; top: 204px; left: 0; width: 1200px; height: 768px; background: linear-gradient(135deg, #3f5a2a 0%, #5f7a3a 40%, #c9a638 62%, #3a4a2a 100%); }
  .hero-title { position: absolute; left: 62px; top: 306px; font-family: "Bebas Neue", sans-serif; font-size: 98px; line-height: 96px; color: var(--white); letter-spacing: 1px; }

  .promo { position: absolute; top: 972px; left: 0; width: 1200px; height: 451px; background: var(--yellow); }
  .anniversary-badge { position: absolute; left: 75px; top: 90px; width: 310px; height: 250px; border-radius: 24px; background: rgba(46, 58, 140, 0.18); }
  .promo-headline { position: absolute; left: 440px; top: 92px; font-family: "Bebas Neue", sans-serif; font-size: 82px; line-height: 1; color: var(--navy); letter-spacing: 1px; }
  .promo-sub { position: absolute; left: 440px; top: 192px; font-family: "Bebas Neue", sans-serif; font-size: 60px; line-height: 1; color: #2a2a2a; letter-spacing: 1px; }
  .signup-button { position: absolute; left: 440px; top: 291px; width: 278px; height: 91px; border-radius: 46px; background: var(--navy); color: var(--white); font-family: "Bebas Neue", sans-serif; font-size: 46px; display: flex; align-items: center; justify-content: center; letter-spacing: 1px; text-decoration: none; }

  .academy { position: absolute; top: 1490px; left: 0; width: 1200px; text-align: center; }
  .academy-title { font-family: "Oswald", sans-serif; font-weight: 500; font-size: 46px; color: var(--navy); transform: scaleX(0.85); letter-spacing: 1px; }
  .academy-text { width: 1000px; margin: 24px auto 0; font-size: 27px; line-height: 54px; color: var(--muted); }

  .info-card { position: absolute; top: 1838px; height: 660px; width: 563px; background: var(--white); box-shadow: 0 0 8px rgba(0,0,0,0.14); }
  .info-card.dates { left: 18px; }
  .info-card.pricing { left: 616px; }
  .card-head { height: 90px; background: var(--navy); color: var(--white); font-family: "Oswald", sans-serif; font-size: 33px; padding-left: 37px; display: flex; align-items: center; }
  .card-head span { display: inline-block; transform: scaleX(0.88); transform-origin: left; }
  .card-body { padding: 40px 36px 0; font-size: 24px; color: var(--muted); }
  .week { margin-bottom: 22px; line-height: 42px; }
  .week-label { font-weight: 600; color: #444; }
  .price-line { line-height: 42px; margin-bottom: 42px; }
  .price-line:first-child { margin-top: 0; }
  .save { color: var(--navy); font-weight: 600; }

  .series-band { position: absolute; top: 2604px; left: 0; width: 1200px; height: 309px; background: var(--navy); text-align: center; font-family: "Oswald", sans-serif; font-size: 72px; line-height: 96px; color: var(--white); padding-top: 54px; }
  .series-band p { transform: scaleX(0.86); }
  .series-accent { color: var(--gold); }

  .objectives-photo { position: absolute; left: 34px; top: 2988px; width: 564px; height: 518px; background: linear-gradient(160deg, #f0c03a 0%, #b98a52 45%, #8a6a45 100%); }
  .objectives-title { position: absolute; left: 646px; top: 3008px; font-family: "Oswald", sans-serif; font-size: 60px; color: #2a2a2a; transform: scaleX(0.84); transform-origin: left; line-height: 1.2; }
  .objectives-rule { position: absolute; left: 649px; top: 3091px; width: 92px; height: 5px; background: var(--navy); }
  .objectives-text { position: absolute; left: 650px; top: 3126px; width: 502px; font-family: "Roboto", sans-serif; font-size: 24px; line-height: 45px; color: var(--muted); text-align: justify; }

  .site-footer { position: absolute; top: 3582px; left: 0; width: 1200px; height: 122px; background: var(--footer); color: var(--white); font-size: 24px; font-weight: 500; display: flex; align-items: center; justify-content: center; }
</style>
</head>
<body>
  <header class="site-header">
    <div class="brand-dot"></div>
    <div class="brand-name">Hemmingtarn</div>
  </header>

  <section class="hero" role="img" aria-label="Young campers in yellow camp shirts and caps standing in front of a tall cornfield">
    <h1 class="hero-title">Hemmingtarn<br>Baseball Camp</h1>
  </section>

  <section class="promo">
    <div class="anniversary-badge" role="img" aria-label="22 years anniversary celebration badge"></div>
    <h2 class="promo-headline">Learn to play like a pro</h2>
    <p class="promo-sub">Sign up today and save money</p>
    <a class="signup-button" href="https://hemmingtarn.com/">Sign Up</a>
  </section>

  <section class="academy">
    <h2 class="academy-title">HEMMINGTARN BASEBALL ACADEMY</h2>
    <p class="academy-text">This is the place to be if you are looking to give your child a baseball experience second to none! This camp is geared toward baseball players ages 5 to 14 who are looking to improve their skills and knowledge of the game.</p>
  </section>

  <article class="info-card dates">
    <div class="card-head"><span>2022 CAMP DATES</span></div>
    <div class="card-body">
      <div class="week"><div class="week-label">WEEK 1 :</div>June 27 - July 1 @Alder Bend Park - Marrowfield</div>
      <div class="week"><div class="week-label">WEEK 2 :</div>July 11 - July 15 @Tollen Park-Ashcombe</div>
      <div class="week"><div class="week-label">WEEK 3 :</div>July 18 - July 22 @Alder Bend Road Park<br>Marrowfield</div>
      <div class="week"><div class="week-label">WEEK 4 :</div>July 25 - July 29 @Alder Bend Road Park -<br>Marrowfield</div>
    </div>
  </article>

  <article class="info-card pricing">
    <div class="card-head"><span>2022 PRICING</span></div>
    <div class="card-body">
      <div class="price-line">Half Day (5 year olds only) - $225</div>
      <div class="price-line">Full Day 1 Week - $350</div>
      <div class="price-line">Full Day 2 Week - $650 - <span class="save">Save $50</span></div>
      <div class="price-line">Full Day 3 Week - $925 - <span class="save">Save $125</span></div>
      <div class="price-line">Full Day 4 Week - $1,125 - <span class="save">Save $275</span></div>
    </div>
  </article>

  <section class="series-band">
    <p>IT'S 22ND YEAR RUNNING A</p>
    <p><span class="series-accent">4-5 WEEK SERIES</span> OF SUMMER CAMPS</p>
  </section>

  <div class="objectives-photo" role="img" aria-label="Campers in yellow shirts running the bases during a drill on a dirt infield"></div>
  <h2 class="objectives-title">CAMP OBJECTIVES</h2>
  <div class="objectives-rule"></div>
  <p class="objectives-text">HEMMINGTARN BASEBALL CAMP provides a safe, fun, &amp; educational environment where beginner, as well as experienced players can excel. Throughout the week, your child will learn the basic fundamentals of the game and be able to specialize in the position of their choice. Each camper will learn the importance of team work, sportsmanship, and fair play.</p>

  <footer class="site-footer">© Copyrights 2020-HT.All Rights Reserved.</footer>
</body>
</html>
```